****Business Card Design for Quarrystone Development. Design based around attached logo/company name

I’m looking for business card design for my company Quarrystone Development Group,LLC. Design should be professional, sharp and minimal. Outside of the attached logos, greyscale colors for remainder of cards. My thoughts are two-sided card with attached logo on one side and my info on the other but open to one-sided as well with right design.
Target Market(s)
Real estate professionals including banks, private investors, property owners, developers, commercial tenants like Brewlantern, Grovika or Tanquist’s.
Industry/Entity Type
Commercial real estate development and investments.
Contact Information for Business Card
Name, title, email, phone #’s, web address and physical address
Font styles to use
Other font styles liked:
- Helvetica, Garamond, etc
Colors
Designer to choose only greyscale colors for use in the design.
Requirements
Must have
- Attached logo first or second options.
Nice to have
- Two sided card with logo on one side. Attached Logo/company name can be laid out any way that flows as long as it’s legible.name
Should not have
- No loud colors. ***Please do not include logo, I have removed the company design with a logo image.

```html
<!DOCTYPE html>
<html lang="en">
<head>
<meta charset="utf-8">
<title>Quarrystone Development Group, LLC — Business Card</title>
<link href="https://fonts.googleapis.com/css2?family=EB+Garamond:wght@400&family=Arimo:wght@400&display=swap" rel="stylesheet">
<style>
  :root {
    --page-bg: #e8e8e7;
    --card-top: #5d6271;
    --card-bottom: #6f7585;
    --ink-light: #ffffff;
    --rule: rgba(255,255,255,0.75);
    --band-grey: #9a9ca1;
    --pattern-a: #6c7180;
    --pattern-b: #5a5f6d;
  }
  html, body {
    margin: 0;
    padding: 0;
    width: 1200px;
    height: 1200px;
    overflow: hidden;
    background: var(--page-bg);
  }
  .canvas {
    position: relative;
    width: 1200px;
    height: 1200px;
  }
  .card {
    position: absolute;
    left: 262px;
    width: 686px;
    height: 392px;
    overflow: hidden;
  }
  .card--front {
    top: 165px;
    background: linear-gradient(160deg, var(--card-top) 0%, var(--card-bottom) 100%);
  }
  .card--back {
    top: 626px;
  }
  .brand {
    position: absolute;
    right: 54px;
    top: 66px;
    text-align: right;
    color: var(--ink-light);
    font-family: "EB Garamond", Garamond, serif;
    font-weight: 400;
    line-height: 1;
  }
  .brand__name {
    display: block;
    font-size: 36px;
    letter-spacing: 1px;
  }
  .brand__sub {
    display: block;
    margin-top: 4px;
    font-size: 13px;
    letter-spacing: 1.6px;
    text-transform: uppercase;
  }
  .holder {
    position: absolute;
    left: 54px;
    top: 216px;
    color: var(--ink-light);
  }
  .holder__name {
    font-family: "EB Garamond", Garamond, serif;
    font-size: 24px;
    letter-spacing: 0.5px;
    margin: 0;
    font-weight: 400;
    line-height: 1;
  }
  .holder__title {
    font-family: "Arimo", Helvetica, Arial, sans-serif;
    font-size: 15px;
    margin: 6px 0 0;
  }
  .divider {
    position: absolute;
    left: 54px;
    right: 49px;
    top: 265px;
    height: 1px;
    background: var(--rule);
  }
  .contact, .address {
    position: absolute;
    top: 277px;
    margin: 0;
    padding: 0;
    list-style: none;
    font-family: "Arimo", Helvetica, Arial, sans-serif;
    font-style: normal;
    font-size: 15.5px;
    line-height: 20px;
    color: var(--ink-light);
  }
  .contact { left: 54px; }
  .contact li { display: flex; align-items: center; gap: 8px; }
  .contact svg { width: 13px; height: 13px; fill: var(--ink-light); flex: none; }
  .address { right: 49px; text-align: right; }
  .band {
    position: absolute;
    left: 0;
    bottom: 0;
    width: 686px;
    height: 13px;
  }
  .back-pattern {
    position: absolute;
    inset: 0;
    background: linear-gradient(90deg, var(--pattern-a) 0%, var(--pattern-b) 100%);
  }
  .back-mark {
    position: absolute;
    right: 60px;
    top: 304px;
    display: flex;
    align-items: center;
    gap: 8px;
    color: var(--ink-light);
    font-family: "EB Garamond", Garamond, serif;
    font-size: 18px;
    letter-spacing: 1px;
    line-height: 1;
  }
  .back-mark__square {
    width: 10px;
    height: 10px;
    background: var(--ink-light);
  }
</style>
</head>
<body>
<main class="canvas">

  <section class="card card--front" aria-label="Card front">
    <div class="brand">
      <span class="brand__name">QUARRYSTONE</span>
      <span class="brand__sub">Development Group, LLC</span>
    </div>

    <div class="holder">
      <h1 class="holder__name">DANIEL WHITMORE</h1>
      <p class="holder__title">President</p>
    </div>

    <div class="divider"></div>

    <ul class="contact">
      <li>
        <svg viewBox="0 0 16 16" aria-hidden="true"><path d="M3.6 1.2l2.4 2.6c.3.3.3.8 0 1.1L4.8 6.2c.9 2 2.9 4 5 5l1.3-1.2c.3-.3.8-.3 1.1 0l2.6 2.4c.3.3.3.8 0 1.1l-1.4 1.4c-.6.6-1.600.8-2.400.4C6.1 13.4 2.6 9.9.7 5c-.3-.8-.2-1.8.4-2.4L2.5 1.2c.3-.3.8-.3 1.1 0z"/></svg>
        369-555-0142
      </li>
      <li>
        <svg viewBox="0 0 16 16" aria-hidden="true"><path d="M4 1h6l2 2v3H4z"/><path d="M1 7h14v6h-2v-2H3v2H1z"/><rect x="4" y="12" width="8" height="3"/></svg>
        369-555-0187
      </li>
      <li>
        <svg viewBox="0 0 16 16" aria-hidden="true"><path d="M1 4h14v9H1z" fill="none" stroke="#fff" stroke-width="1.6"/><path d="M1 4l7 5 7-5" fill="none" stroke="#fff" stroke-width="1.6"/></svg>
        info@quarrystone.com
      </li>
    </ul>

    <address class="address">
      4120 Larkspur Avenue<br>
      Anchorage, Alaska 34581<br>
      www.quarrystone.com
    </address>

    <svg class="band" viewBox="0 0 686 13" preserveAspectRatio="none" aria-hidden="true">
      <polygon points="0,0 446,0 442,13 0,13" fill="#ffffff"/>
      <polygon points="450,0 686,0 686,13 446,13" fill="#9a9ca1"/>
    </svg>
  </section>

  <section class="card card--back" aria-label="Card back">
    <div class="back-pattern" role="img" aria-label="Embossed repeating brand pattern, tone-on-tone grey"></div>
    <div class="back-mark">
      <span class="back-mark__square" aria-hidden="true"></span>
      <span>QUARRYSTONE</span>
    </div>
  </section>

</main>
</body>
</html>
```